TalkHarbor - Language Coaching Services

Sleek, innovative, trendy design for Language Coaching business.

TalkHarbor is a new UK based company that provides Language Coaching services. We offer highly personalized on-line and face to face language courses. We also impart learning techniques workshops based on the latest neuroscience research for second-language acquisition.

Target Market(s)

See attached info

Industry/Entity Type

Consulting

Contact Information for Business Card

TalkHarbor
DaniaKV@talkharbor.co.uk
TalkHarbor.co.uk
London, UK

Font styles to use
Sans Serif

```html
<!DOCTYPE html>
<html lang="en">
<head>
<meta charset="utf-8">
<title>TalkHarbor Business Cards</title>
<link rel="stylesheet" href="https://fonts.googleapis.com/css2?family=Montserrat:wght@500&family=Arimo:wght@400;700&display=swap">
<style>
  :root {
    --page-bg: #2b2b2b;
    --card-white: #f6f7f8;
    --brand-blue: #1b5a85;
    --brand-blue-light: #2c86b6;
    --ink-white: #ffffff;
    --ink-soft: #dbe7f0;
  }
  * { margin: 0; padding: 0; box-sizing: border-box; }
  html, body {
    width: 1200px;
    height: 997px;
    overflow: hidden;
    background: var(--page-bg);
  }
  .stage {
    position: relative;
    width: 1200px;
    height: 997px;
  }
  .card {
    position: absolute;
    width: 600px;
    height: 343px;
    border-radius: 22px;
    overflow: hidden;
    background: linear-gradient(160deg, #ffffff 0%, var(--card-white) 60%, #e9ecef 100%);
  }
  .card svg.card-shapes {
    position: absolute;
    inset: 0;
    width: 100%;
    height: 100%;
  }
  .card--back { left: 100px; top: 120px; }
  .card--front { left: 500px; top: 520px; }

  .brand-circle {
    position: absolute;
    border-radius: 50%;
    border: 7px solid var(--brand-blue-light);
  }
  .wordmark {
    position: absolute;
    font-family: "Montserrat", sans-serif;
    font-weight: 500;
    color: var(--brand-blue-light);
    letter-spacing: 0.04em;
    white-space: nowrap;
    line-height: 1;
  }

  /* back card */
  .card--back .wordmark { left: 48px; top: 76px; font-size: 52px; }
  .card--back .brand-circle { left: 262px; top: 140px; width: 88px; height: 88px; }
  .website {
    position: absolute;
    left: 452px;
    top: 264px;
    font-family: "Arimo", sans-serif;
    font-weight: 700;
    font-size: 15px;
    letter-spacing: 0.14em;
    color: var(--ink-white);
    white-space: nowrap;
    transform: translate(-50%, -50%) rotate(-30deg);
  }

  /* front card */
  .card--front .brand-circle { left: 256px; top: 16px; width: 88px; height: 88px; }
  .card--front .wordmark {
    left: 0;
    width: 100%;
    text-align: center;
    top: 114px;
    font-size: 44px;
  }

  .person {
    position: absolute;
    right: 268px;
    top: 252px;
    text-align right;
    text-align: right;
    font-family: "Arimo", sans-serif;
    color: var(--ink-white);
  }
  .person__name { font-weight: 700; font-size: 17px; letter-spacing: 0.02em; }
  .person__role { font-size: 16px; color: var(--ink-soft); margin-top: 2px; }

  .divider {
    position: absolute;
    left: 346px;
    top: 236px;
    width: 1px;
    height: 76px;
    background: rgba(255, 255, 255, 0.45);
  }
  .contacts {
    position: absolute;
    left: 362px;
    top: 234px;
    list-style: none;
    font-family: "Arimo", sans-serif;
    font-size: 16px;
    color: var(--ink-white);
  }
  .contacts li {
    display: flex;
    align-items: center;
    gap: 10px;
    height: 30px;
  }
  .contacts svg { width: 18px; height: 18px; flex: none; }
</style>
</head>
<body>
<main class="stage">

  <section class="card card--back" aria-label="Business card, back">
    <svg class="card-shapes" viewBox="0 0 600 343" aria-hidden="true">
      <path d="M230,343 Q400,230 600,125 L600,343 Z" fill="var(--brand-blue)"/>
      <path d="M170,343 Q380,205 596,112 Q390,222 210,343 Z" fill="var(--brand-blue-light)"/>
    </svg>
    <div class="wordmark">TALKHARBOR</div>
    <div class="brand-circle"></div>
    <div class="website">WWW.TALKHARBOR.CO.UK</div>
  </section>

  <section class="card card--front" aria-label="Business card, front">
    <svg class="card-shapes" viewBox="0 0 600 343" aria-hidden="true">
      <path d="M0,330 Q260,200 600,205 L600,343 L0,343 Z" fill="var(--brand-blue)"/>
      <path d="M40,312 Q280,180 575,190 Q290,205 40,312 Z" fill="var(--brand-blue-light)"/>
    </svg>
    <div class="brand-circle"></div>
    <div class="wordmark">TALKHARBOR</div>

    <div class="person">
      <div class="person__name">OWEN TALLIS</div>
      <div class="person__role">Director</div>
    </div>
    <div class="divider"></div>
    <ul class="contacts">
      <li>
        <svg viewBox="0 0 18 18" aria-hidden="true">
          <circle cx="9" cy="9" r="9" fill="var(--ink-white)"/>
          <path d="M5.5,6.5 Q9,4 12.5,6.5 L11.5,8 L10,7.4 L8,7.4 L6.5,8 Z M6.5,9 L11.5,9 L12,12.5 L6,12.5 Z" fill="var(--brand-blue)"/>
        </svg>
        <span>0400 118 224</span>
      </li>
      <li>
        <svg viewBox="0 0 18 18" aria-hidden="true">
          <circle cx="9" cy="9" r="9" fill="var(--ink-white)"/>
          <rect x="4.5" y="6" width="9" height="6.5" fill="var(--brand-blue)"/>
          <path d="M4.5,6 L9,9.6 L13.5,6" fill="none" stroke="var(--ink-white)" stroke-width="1"/>
        </svg>
        <span>owen@talkharbor.co.uk</span>
      </li>
    </ul>
  </section>

</main>
</body>
</html>
```